Revamp of existing namecard

Existingly, i've got a namecard that i would like to retain the main design. but there are some changes in my company and i would need to do some amendments to it.

We are a money transfer and money exchange company.
I need 2 different types of name card.
1. For individual name cards
the front to put the following:
Company name and logo
English Name, Chinese Name appointment
Mobile Number, Email and Website.
2 License number under the logo and name

the back of the name card to put
8 address: 7 Singapore and 1 Hong Kong branch addresses
8 Mobile Number of the corresponding addresses.

We would like to retain the name card front design
the name card back design can change but color to retain.

2nd name card is generic name card
Front:
Company name and logo
Branch Mobile Number, Branch Address, Email and Website.

Industry/Entity Type

remittance and money exchange

Contact Information for Business Card

I need 2 different types of name card. 1. For individual name cards the front to put the following: Company name and logo English Name, Chinese Name appointment Mobile Number, Email and Website. 2 License number under the logo and name the back of the name card to put 8 address: 7 Singapore and 1 Hong Kong branch addresses 8 Mobile Number of the corresponding addresses. We would like to retain the name card front design the name card back design can change but color to retain. 2nd name card is generic name card Front: the front to put the following: Company name and logo Branch Mobile Number, Branch Address, Email and Website. 2 License number under the logo and name

Requirements
Must have
• I need 2 different types of name card. 1. For individual name cards the front to put the following: Company name and logo English Name, Chinese Name appointment Mobile Number, Email and Website. 2 License number under the logo and name the back of the name card to put 8 address: 7 Singapore and 1 Hong Kong branch addresses 8 Mobile Number of the corresponding addresses. We would like to retain the name card front design the name card back design can change but color to retain. 2nd name card is generic name card Front: the front to put the following: Company name and logo Branch Mobile Number, Branch Address, Email and Website. 2 License number under the logo and name
Nice to have
• use back color code

```html
<!DOCTYPE html>
<html lang="en">
<head>
<meta charset="utf-8">
<title>Veranta business cards</title>
<link rel="stylesheet" href="https://fonts.googleapis.com/css2?family=Montserrat:wght@400;500;600;700&family=Noto+Sans+TC:wght@700&display=swap">
<style>
  :root {
    --teal: #6cc5d1;
    --ink: #262d38;
    --paper: #ffffff;
    --ghost: #f1f6f8;
    --backdrop: #a3a3a3;
  }
  * { box-sizing: border-box; margin: 0; padding: 0; }
  html, body { width: 1072px; height: 1200px; overflow: hidden; }
  body {
    background: var(--backdrop);
    font-family: "Montserrat", Arial, sans-serif;
    color: var(--ink);
    position: relative;
  }
  .card {
    position: absolute;
    left: 86px;
    width: 900px;
    height: 515px;
    background: var(--paper);
    overflow: hidden;
  }
  .card--back { top: 70px; }
  .card--front { top: 615px; }

  .ghost-mark {
    position: absolute;
    width: 560px;
    height: 560px;
    border-radius: 50%;
    background: var(--ghost);
    top: -20px;
  }
  .card--back .ghost-mark { left: 130px; }
  .card--front .ghost-mark { left: 150px; }

  .accent-bar {
    position: absolute;
    bottom: 0;
    height: 12px;
  }
  .accent-bar--teal { left: 0; width: 415px; background: var(--teal); border-top-right-radius: 6px; }
  .accent-bar--ink { right: 0; width: 415px; background: var(--ink); border-top-left-radius: 6px; }

  .brand {
    position: absolute;
    display: flex;
    align-items: center;
    font-weight: 600;
    color: var(--ink);
    letter-spacing: 0.01em;
  }
  .brand__dot {
    background: var(--teal);
    border-radius: 6px;
    flex: none;
  }
  .card--back .brand { left: 165px; top: 218px; font-size: 70px; gap: 22px; }
  .card--back .brand__dot { width: 62px; height: 62px; border-radius: 10px; }
  .card--front .brand { left: 44px; top: 62px; font-size: 38px; gap: 14px; }
  .card--front .brand__dot { width: 36px; height: 36px; }

  .branch-note {
    position: absolute;
    left: 0; right: 0;
    bottom: 30px;
    text-align: center;
    font-size: 20px;
    font-weight: 600;
  }

  .person {
    position: absolute;
    right: 55px;
    top: 60px;
    text-align: right;
  }
  .person__name { font-size: 40px; font-weight: 700; line-height: 1.15; }
  .person__name-zh { font-family: "Noto Sans TC", "Montserrat", sans-serif; font-size: 40px; font-weight: 700; line-height: 1.15; }
  .person__role { margin-top: 14px; color: var(--teal); font-size: 21px; line-height: 1.25; }

  .contacts {
    position: absolute;
    bottom: 52px;
    font-size: 21px;
    line-height: 34px;
    font-weight: 500;
  }
  .contacts--phones { left: 40px; }
  .contacts--web { right: 55px; text-align: right; }
  .contacts li { list-style: none; display: flex; align-items: center; gap: 12px; }
  .contacts--web li { justify-content: flex-end; }
  .contacts svg { width: 14px; height: 14px; fill: var(--ink); flex: none; }
</style>
</head>
<body>

<section class="card card--back" aria-label="Card back">
  <div class="ghost-mark" aria-hidden="true"></div>
  <div class="brand"><span class="brand__dot"></span>VERANTA</div>
  <p class="branch-note">7 Singapore and 1 Hong Kong branch addresses</p>
  <div class="accent-bar accent-bar--teal"></div>
  <div class="accent-bar accent-bar--ink"></div>
</section>

<section class="card card--front" aria-label="Card front">
  <div class="ghost-mark" aria-hidden="true"></div>
  <div class="brand"><span class="brand__dot"></span>VERANTA</div>

  <div class="person">
    <p class="person__name">Marcus Lee</p>
    <p class="person__name-zh">李家明</p>
    <p class="person__role">Director of<br>Business Development</p>
  </div>

  <ul class="contacts contacts--phones">
    <li>
      <svg viewBox="0 0 14 14" aria-hidden="true"><path d="M4 0h6a1 1 0 0 1 1 1v12a1 1 0 0 1-1 1H4a1 1 0 0 1-1-1V1a1 1 0 0 1 1-1zm.6 1.6v9.6h4.8V1.6z"/></svg>
      + 852 5120 4387
    </li>
    <li>
      <svg viewBox="0 0 14 14" aria-hidden="true"><path d="M3 1l2.2 2.6-1.3 1.6a8 8 0 0 0 4.9 4.9l1.6-1.3L13 11l-1.6 2C6 13 1 8 1 2.6z"/></svg>
      + 852 6231 0958
    </li>
  </ul>

  <ul class="contacts contacts--web">
    <li>
      marcus@veranta.com.hk
      <svg viewBox="0 0 14 14" aria-hidden="true"><path d="M1 3h12v8H1zm1.2 1.2L7 7.6l4.8-3.4z"/></svg>
    </li>
    <li>
      www.veranta.com.hk
      <svg viewBox="0 0 14 14" aria-hidden="true"><path d="M7 1a6 6 0 1 0 0 12A6 6 0 0 0 7 1zm0 1.3c.6 0 1.5 1.6 1.7 4H5.3C5.5 3.9 6.4 2.3 7 2.3zM5.3 7.7h3.4c-.2 2.4-1.1 4-1.7 4s-1.5-1.6-1.7-4zM2.4 7.7H4a9 9 0 0 0 .8 3.5 4.7 4.7 0 0 1-2.4-3.5zm0-1.4a4.7 4.7 0 0 1 2.4-3.5A9 9 0 0 0 4 6.3zm7.6 1.4h1.6a4.7 4.7 0 0 1-2.4 3.5 9 9 0 0 0 .8-3.5zm0-1.4a9 9 0 0 0-.8-3.5 4.7 4.7 0 0 1 2.4 3.5z"/></svg>
    </li>
  </ul>

  <div class="accent-bar accent-bar--teal"></div>
  <div class="accent-bar accent-bar--ink"></div>
</section>

</body>
</html>
```